Verdel Harvest - Stationery Design Project

We need a stationary for our business. We grow roots and fruits in Central and South America, we import and distribute in FL, USA. We do fresh and frozen products.

Target Market(s)

Small and big supermarkets, wholesalers, traders, distributors, etc

Industry/Entity Type

Business

```html
<!DOCTYPE html>
<html lang="en">
<head>
<meta charset="UTF-8">
<title>Verdel Harvest – Envelope</title>
<link rel="stylesheet" href="https://fonts.googleapis.com/css2?family=Montserrat:wght@500&display=swap">
<style>
  :root {
    --brand-orange: #ff6a06;
    --brand-green: #3f5f1a;
    --paper: #ffffff;
    --edge: #4a4a4a;
    --foliage: #8fd84a;
    --trunk: #6b2a2a;
  }
  html, body {
    margin: 0;
    padding: 0;
    width: 1200px;
    height: 429px;
    overflow: hidden;
    background: var(--paper);
  }
  .stationery {
    position: relative;
    width: 1200px;
    height: 429px;
  }
  .envelope-art {
    position: absolute;
    inset: 0;
  }
  .brand-name {
    position: absolute;
    left: 140px;
    top: 150px;
    width: 265px;
    margin: 0;
    text-align: center;
    font-family: "Montserrat", sans-serif;
    font-weight: 500;
    font-size: 29px;
    letter-spacing: 0.5px;
    line-height: 1;
    color: var(--brand-green);
    white-space: nowrap;
  }
</style>
</head>
<body>
<main class="stationery">
  <svg class="envelope-art" width="1200" height="429" viewBox="0 0 1200 429" xmlns="http://www.w3.org/2000/svg">
    <defs>
      <linearGradient id="footer-fade" x1="0" x2="1" y1="0" y2="0">
        <stop offset="0" stop-color="#ff6a06" stop-opacity="0"/>
        <stop offset="1" stop-color="#ff6a06"/>
      </linearGradient>
      <linearGradient id="orchard-tones" x1="0" x2="0" y1="0" y2="1">
        <stop offset="0" stop-color="#8fd84a"/>
        <stop offset="0.6" stop-color="#a8d870" stop-opacity="0.8"/>
        <stop offset="1" stop-color="#6b2a2a" stop-opacity="0.6"/>
      </linearGradient>
    </defs>

    <!-- back of envelope -->
    <g class="envelope-back">
      <rect x="338" y="17" width="812" height="355" fill="var(--paper)" stroke="var(--edge)" stroke-width="1"/>
      <path class="flap" d="M338 17 H1150 V72 Q1150 100 1120 100 H338 Z" fill="var(--brand-orange)"/>
      <path class="side-fold" d="M1120 100 Q1122 110 1122 130 V345 Q1122 368 1138 372" fill="none" stroke="var(--edge)" stroke-width="1"/>
    </g>

    <!-- front of envelope -->
    <g class="envelope-front">
      <rect x="48" y="56" width="814" height="354" fill="var(--paper)" stroke="var(--edge)" stroke-width="1"/>
      <rect class="top-band" x="48" y="56" width="814" height="22" fill="var(--brand-orange)"/>
      <rect class="address-window" x="123" y="280" width="301" height="87" rx="14" fill="var(--paper)" stroke="var(--edge)" stroke-width="1"/>
      <rect class="footer-line" x="540" y="404" width="322" height="5" fill="url(#footer-fade)"/>
      <rect class="orchard-illustration" x="776" y="272" width="86" height="134" rx="30" fill="url(#orchard-tones)" role="img" aria-label="Illustration of a fruit tree with green leaves and red fruit"/>
    </g>
  </svg>

  <p class="brand-name">VERDEL HARVEST</p>
</main>
</body>
</html>
```